Stationary design for new digital markerting company

I need a stationary design for a new digital marketing company called Mossy Lantern.
We work with businesses to help them create and increase their online presence in order to increase awareness of their brand.
The design must keep with the colour schemes of our logo.
I would like a design that stands out but isn't over the top while also being professional and sophisticated.

Target Market(s)

other businesses

Industry/Entity Type

Business Consultant

Font styles to use
Sans Serif

Colors
abd036
ffffff
a54499

Requirements
Must have
• logo, plus the same colour scheme

```html
<!DOCTYPE html>
<html lang="en">
<head>
<meta charset="utf-8">
<title>Mossy Lantern – Business Cards</title>
<link href="https://fonts.googleapis.com/css2?family=Mulish:wght@400;600;800&display=swap" rel="stylesheet">
<style>
  :root {
    --purple: #a54499;
    --purple-deep: #8c1d6e;
    --green: #abd036;
    --green-deep: #7dbb1c;
    --white: #ffffff;
    --ink: #444444;
    --backdrop: #e4e6e8;
    --ghost: #eef0f1;
  }
  * { box-sizing: border-box; margin: 0; padding: 0; }
  html, body {
    width: 1200px; height: 1000px; overflow: hidden;
    background: var(--backdrop);
    font-family: "Mulish", sans-serif;
  }
  .stage {
    position: relative; width: 1200px; height: 1000px;
  }
  .card {
    position: absolute; left: 330px;
    width: 540px; height: 309px;
    overflow: hidden;
    box-shadow: 0 10px 30px rgba(0,0,0,0.12);
  }
  /* Front */
  .card--front {
    top: 130px;
    background: var(--purple-deep);
    display: flex; align-items: center; justify-content: center; gap: 22px;
  }
  .brand-dot {
    border-radius: 50%; background: var(--green-deep); flex: none;
  }
  .card--front .brand-dot { width: 78px; height: 78px; }
  .brand-name {
    font-weight: 600; letter-spacing: 2px; text-transform: uppercase; line-height: 1;
  }
  .card--front .brand-name { color: var(--white); font-size: 40px; }
  .tagline {
    font-size: 12px; letter-spacing: 4px; margin-top: 8px;
  }
  .card--front .tagline { color: var(--white); }

  /* Back */
  .card--back {
    top: 530px;
    background: var(--white);
  }
  .ghost-circle {
    position: absolute; right: -70px; top: 95px;
    width: 210px; height: 210px; border-radius: 50%;
    background: var(--ghost);
  }
  .back-brand {
    position: absolute; left: 150px; top: 28px;
    display: flex; align-items: center; gap: 12px;
  }
  .card--back .brand-dot { width: 40px; height: 40px; }
  .card--back .brand-name { color: var(--purple-deep); font-size: 24px; }
  .card--back .tagline { color: var(--ink); font-size: 8px; letter-spacing: 3px; margin-top: 4px; }

  .contact {
    position: absolute; left: 30px; top: 92px;
    font-size: 12px; color: var(--ink); line-height: 1.45; list-style: none;
  }
  .contact li { display: flex; align-items: center; gap: 7px; }
  .contact .icon {
    width: 11px; height: 11px; background: var(--green-deep); border-radius: 2px; flex: none;
  }
  .contact .address { padding-left: 0; margin-top: 2px; }

  .person {
    position: absolute; right: 120px; bottom: 44px; text-align: left;
  }
  .person-name {
    color: var(--purple-deep); font-weight: 800; font-size: 17px; letter-spacing: 1px;
  }
  .person-role { color: var(--ink); font-size: 13px; margin-top: 2px; }

  .edge-bands { position: absolute; left: 0; bottom: 0; width: 540px; height: 14px; }
</style>
</head>
<body>
<main class="stage">

  <section class="card card--front" aria-label="Business card front">
    <span class="brand-dot"></span>
    <div>
      <p class="brand-name">Mossy Lantern</p>
      <p class="tagline">Glowing Up the Page Ranks</p>
    </div>
  </section>

  <section class="card card--back" aria-label="Business card back">
    <span class="ghost-circle"></span>

    <div class="back-brand">
      <span class="brand-dot"></span>
      <div>
        <p class="brand-name">Mossy Lantern</p>
        <p class="tagline">Glowing Up the Page Ranks</p>
      </div>
    </div>

    <ul class="contact">
      <li><span class="icon"></span>1300 555 018</li>
      <li><span class="icon"></span>hello@mossylantern.com</li>
      <li><span class="icon"></span>www.mossylantern.com</li>
      <li class="address">Level 12, Harbour House</li>
      <li class="address">18 Quay Lane, Sydney</li>
    </ul>

    <div class="person">
      <p class="person-name">JORDAN PELL</p>
      <p class="person-role">Managing Director</p>
    </div>

    <svg class="edge-bands" viewBox="0 0 540 14" preserveAspectRatio="none" aria-hidden="true">
      <polygon points="0,6 215,6 207,14 0,14" fill="var(--purple-deep)"/>
      <polygon points="215,0 540,0 540,14 201,14" fill="var(--green-deep)"/>
    </svg>
  </section>

</main>
</body>
</html>
```